Jolly Hounds Dog Behaviour, Training and Natural Healthcare Business Card Design

I am an experienced and qualified dog behavioural trainer and natural animal healthcare consultant offering a range of services to help pet dog owners with the "whole dog".
COLOURS: A soft light blue in the background - can be fading out or split, red should also feature
LOGO: Dog, healing hands, silhouette, shadow
SERVICES: Behaviour Consults, Training, Complex Skills Coaching Walking Coaching, Diet & Nutrition, Environmental Enrichment, Lifestyle and Lifestage Adaptations, Massage, Natural Health Options
BY LINE: Happy Dogs, Happy Owners
VALUES: Promoting communication and connection between dogs and their owners.
FOCUS: Nutritional guidance and environmental adaptation are often needed to complete the package and increase the success rate of training and behaviour modification.

Target Market(s)

Everyone who has a dog who they wish to improve their relationship with

Industry/Entity Type

Communication

Contact Information for Business Card

Jolly Hounds, Rebecca Thornbury, 0427 861350, jollyhounds7@fernpost.example, www.jollyhounds7.example, Qualified Dog Behavioural Trainer and Natural Animal Healthcare Consultant

Font styles to use
Sans Serif
Script

Colors
85cae6
ec2027

Requirements
Must have
• A clear indication that it is a dog services business. A raised feature
Should not have
• Pawprints, cartoons

```html
<!DOCTYPE html>
<html lang="en">
<head>
<meta charset="utf-8">
<title>Jolly Hounds – Business Card</title>
<link rel="stylesheet" href="https://fonts.googleapis.com/css2?family=Source+Sans+3:wght@400;600;700&display=swap">
<style>
  :root {
    --brand-red: #ec2027;
    --brand-blue: #85cae6;
    --card-white: #ffffff;
    --stage: #e9e9ea;
    --photo-light: #f3ede4;
    --photo-warm: #d9b27a;
  }
  * { box-sizing: border-box; margin: 0; padding: 0; }
  html, body {
    width: 1200px; height: 900px; overflow: hidden;
    background: var(--stage);
    font-family: "Source Sans 3", Arial, sans-serif;
  }
  .canvas {
    position: relative; width: 1200px; height: 900px;
    display: flex; align-items: center; justify-content: center;
  }
  .card {
    position: relative; width: 1000px; height: 572px;
    background: var(--card-white);
    overflow: hidden;
    box-shadow: 0 6px 24px rgba(0,0,0,.18);
  }
  .card-art { position: absolute; inset: 0; }
  .brand {
    position: absolute; top: 34px; left: 520px; width: 440px;
    text-align: right; color: var(--brand-red);
  }
  .brand-name { font-size: 66px; font-weight: 600; line-height: 1; letter-spacing: -0.5px; }
  .brand-tagline { margin-top: 6px; font-size: 21px; font-weight: 400; line-height: 1.15; }
  .contact-person {
    position: absolute; top: 318px; left: 640px; color: var(--card-white);
  }
  .person-name { font-size: 44px; font-weight: 400; line-height: 1.1; letter-spacing: -0.3px; }
  .person-phone { font-size: 30px; font-weight: 700; letter-spacing: 1px; }
  .contact-line {
    position: absolute; display: flex; align-items: center; gap: 14px;
    color: var(--card-white); font-size: 28px; font-weight: 400; letter-spacing: 0.5px;
  }
  .contact-email { top: 462px; left: 46px; }
  .contact-web { top: 512px; left: 400px; }
  .contact-icon { width: 22px; height: 22px; flex: none; }
</style>
</head>
<body>
<main class="canvas">
  <article class="card">
    <svg class="card-art" viewBox="0 0 1000 572" width="1000" height="572" aria-hidden="false">
      <defs>
        <linearGradient id="photo-tone" x1="0" y1="0" x2="1" y2="0.4">
          <stop offset="0" stop-color="var(--photo-light)"/>
          <stop offset="0.45" stop-color="var(--photo-warm)"/>
          <stop offset="1" stop-color="#ffffff" stop-opacity="0"/>
        </linearGradient>
      </defs>
      <rect class="photo-area" x="0" y="0" width="640" height="440" fill="url(#photo-tone)"
            role="img" aria-label="Photo of a smiling golden retriever puppy"/>
      <path class="band-blue" d="M250 440 Q700 330 1000 150 L1000 175 Q560 420 250 440 Z" fill="var(--brand-blue)"/>
      <path class="band-white-rule" d="M0 442 Q560 420 1000 175" fill="none" stroke="#ffffff" stroke-width="4"/>
      <path class="band-red" d="M0 444 Q560 422 1000 178 L1000 572 L0 572 Z" fill="var(--brand-red)"/>
    </svg>

    <header class="brand">
      <h1 class="brand-name">Jolly Hounds</h1>
      <p class="brand-tagline">Qualified Dog Behavioural<br>Trainer and Natural Animal Healthcare Consultant</p>
    </header>

    <div class="contact-person">
      <p class="person-name">Rebecca Thornbury</p>
      <p class="person-phone">0427 861350</p>
    </div>

    <p class="contact-line contact-email">
      <svg class="contact-icon" viewBox="0 0 22 22" aria-hidden="true">
        <circle cx="11" cy="11" r="10" fill="#ffffff"/>
        <rect x="5" y="7" width="12" height="8" fill="none" stroke="var(--brand-red)" stroke-width="1.6"/>
        <path d="M5 7 L11 12 L17 7" fill="none" stroke="var(--brand-red)" stroke-width="1.6"/>
      </svg>
      jollyhounds7@fernpost.example
    </p>

    <p class="contact-line contact-web">
      <svg class="contact-icon" viewBox="0 0 22 22" aria-hidden="true">
        <circle cx="11" cy="11" r="10" fill="#ffffff"/>
        <circle cx="11" cy="11" r="6" fill="none" stroke="var(--brand-red)" stroke-width="1.4"/>
        <ellipse cx="11" cy="11" rx="2.6" ry="6" fill="none" stroke="var(--brand-red)" stroke-width="1.2"/>
        <path d="M5 11 H17" stroke="var(--brand-red)" stroke-width="1.2"/>
      </svg>
      www.jollyhounds7.example
    </p>
  </article>
</main>
</body>
</html>
```